Business Card for a mobile physiotherapy company

I need a layout for a business card for a mobile physiotherapy company.
Slogan is "Mobile Physiotherapy - Your Road To Recovery"
Phone number is 867-555-0142
Email VardenTherapy@postnest.ca (subject to change with website)
Website www.VardenTherapy.ca
My name and credentials: Luke Varden Luke Varden, BSc(kin), MPT, CAFCI, IMS
Information maybe included: Direct Billing, Services including Physiotherapy, IMS, acupuncture
Maybe include facebook and instagram logos
One side with the logo clean and sharp
Other side with details, try not to look too busy, keep everything concise

```html
<!DOCTYPE html>
<html lang="en">
<head>
<meta charset="utf-8">
<title>Varden Therapy – Business Card</title>
<link href="https://fonts.googleapis.com/css2?family=Roboto:ital,wght@0,400;0,500;0,700;1,400&display=swap" rel="stylesheet">
<style>
  :root {
    --backdrop: #ebe7e2;
    --card-white: #ffffff;
    --forest: #0b5249;
    --navy: #2c4877;
    --ink-grey: #555a5f;
    --rule-navy: #2c3e5a;
    --white: #ffffff;
  }
  * { box-sizing: border-box; margin: 0; padding: 0; }
  html, body {
    width: 1125px; height: 1200px; overflow: hidden;
    background: var(--backdrop);
    font-family: "Roboto", Arial, sans-serif;
  }
  .canvas { position: relative; width: 1125px; height: 1200px; }

  .card {
    position: absolute; left: 171px; width: 826px; height: 471px;
    box-shadow: 0 3px 8px rgba(0,0,0,0.25);
  }
  .card--front { top: 106px; background: var(--card-white); }
  .card--back { top: 639px; background: var(--forest); }

  /* Front: brand name */
  .brand {
    position: absolute; left: 0; right: 0; text-align: center;
    font-weight: 700; color: var(--forest);
  }
  .card--front .brand { top: 150px; }
  .brand__name { display: block; font-size: 56px; letter-spacing: 6px; line-height: 1; }
  .brand__sub { display: block; font-size: 24px; letter-spacing: 12px; margin-top: 12px; padding-left: 12px; line-height: 1; }

  /* Front: divider */
  .divider { position: absolute; left: 53px; top: 316px; width: 717px; height: 7px; }
  .divider__thick { position: absolute; left: 0; top: 0; width: 178px; height: 7px; background: var(--forest); }
  .divider__thin { position: absolute; left: 178px; top: 3px; right: 0; height: 1px; background: var(--rule-navy); }

  /* Front: person */
  .person { position: absolute; left: 53px; top: 345px; }
  .person__name { font-size: 29px; font-weight: 700; color: var(--navy); line-height: 1; letter-spacing: 0.2px; }
  .person__credentials { font-size: 19px; font-weight: 500; color: var(--navy); margin-top: 4px; }
  .person__billing { font-size: 20px; font-weight: 500; color: var(--forest); margin-top: 5px; }

  /* Front: contact */
  .contact { position: absolute; right: 53px; top: 346px; list-style: none; text-align: right; }
  .contact__item {
    display: flex; justify-content: flex-end; align-items: center; gap: 9px;
    font-size: 19px; color: var(--ink-grey); line-height: 26px;
  }
  .contact__icon { width: 17px; height: 17px; fill: var(--navy); flex: none; }

  /* Back */
  .social {
    position: absolute; top: 44px; right: 50px;
    display: flex; align-items: center; gap: 8px;
    font-size: 18px; font-weight: 500; color: var(--white);
  }
  .social__dot { width: 16px; height: 16px; border-radius: 50%; background: var(--white); }
  .card--back .brand { top: 172px; color: var(--white); }
  .card--back .brand__name { font-size: 76px; letter-spacing: 8px; }
  .card--back .brand__sub { font-size: 33px; letter-spacing: 17px; padding-left: 17px; margin-top: 20px; }

  .tagline {
    position: absolute; left: 0; right: 0; top: 373px; text-align: center;
    color: var(--white); font-size: 19.5px; line-height: 29px;
  }
  .tagline__slogan { font-style: italic; }
  .tagline__services span + span::before { content: "•"; margin: 0 4px; }
</style>
</head>
<body>
<main class="canvas">

  <section class="card card--front" aria-label="Card front">
    <div class="brand">
      <span class="brand__name">VARDEN</span>
      <span class="brand__sub">THERAPY</span>
    </div>

    <div class="divider"><span class="divider__thick"></span><span class="divider__thin"></span></div>

    <div class="person">
      <p class="person__name">LUKE VARDEN</p>
      <p class="person__credentials">BSc(kin), MPT, CAFCI, IMS</p>
      <p class="person__billing">Direct Billing</p>
    </div>

    <ul class="contact">
      <li class="contact__item">867-555-0142
        <svg class="contact__icon" viewBox="0 0 24 24" aria-hidden="true"><path d="M6.6 10.8a15.1 15.1 0 0 0 6.6 6.6l2.2-2.2a1 1 0 0 1 1-.25 11.4 11.4 0 0 0 3.6.57 1 1 0 0 1 1 1V20a1 1 0 0 1-1 1A17 17 0 0 1 3 4a1 1 0 0 1 1-1h3.5a1 1 0 0 1 1 1c0 1.25.2 2.45.57 3.57a1 1 0 0 1-.25 1z"/></svg>
      </li>
      <li class="contact__item">VardenTherapy@postnest.ca
        <svg class="contact__icon" viewBox="0 0 24 24" aria-hidden="true"><path d="M2 5h20v14H2z" fill="none"/><path d="M2 5h20v2l-10 6L2 7zM2 9l10 6 10-6v10H2z"/></svg>
      </li>
      <li class="contact__item">www.VardenTherapy.ca
        <svg class="contact__icon" viewBox="0 0 24 24" aria-hidden="true"><circle cx="12" cy="12" r="10"/><path d="M7 7c2 0 3 1 3 3s2 2 2 4-1 3-1 5M15 4c0 2 1 3 3 3s2 2 3 3" stroke="#fff" stroke-width="1.6" fill="none"/></svg>
      </li>
    </ul>
  </section>

  <section class="card card--back" aria-label="Card back">
    <div class="social"><span class="social__dot"></span>@VardenTherapy</div>

    <div class="brand">
      <span class="brand__name">VARDEN</span>
      <span class="brand__sub">THERAPY</span>
    </div>

    <div class="tagline">
      <p class="tagline__slogan">Mobile Physiotherapy - Your Road To Recovery</p>
      <p class="tagline__services"><span>Physiotherapy</span><span>IMS</span><span>Acupuncture</span></p>
    </div>
  </section>

</main>
</body>
</html>
```